Oakmere Animal Care Group of Central Pennsylvania

I need a business card design for a new company in Harrisburg PA called "Animal Care Oakmere Group of Central PA". I will be providing relief services for veterinarians who need coverage during vacations; sick/maternity leave, etc. I would like to see the veterinarian symbol incorporated in the design in combination with animals (dogs /cats/birds/reptiles an pocket pets). Include My full name: Tomás R. Quintaval DVM, MLAS, BS. Also include my e mail (dvmtrq@mailbrook.net) and phone number 5552846017

Target Market(s)

Small Animal Veterinarian, practice owner

Industry/Entity Type

Business

Contact Information for Business Card

Oakmere Animal Care Group of Central PA

Font styles to use
Script

Requirements
Must have
• Veterinarian caduceus (see image) and Small animals (pets) within the logo.
Nice to have
• Give a sense of relaxation (vacationing)
Should not have
• Large animals, i.e. horses, cows, zoo animals...

```html
<!DOCTYPE html>
<html lang="en">
<head>
<meta charset="utf-8">
<title>Animal Care Oakmere Group of Central PA — Business Card</title>
<link href="https://fonts.googleapis.com/css2?family=Great+Vibes&family=Cinzel:wght@500&family=Roboto:wght@400&display=swap" rel="stylesheet">
<style>
  :root {
    --page-bg: #e9e6e1;
    --card-white: #ffffff;
    --band-black: #0d0d0d;
    --brand-red: #c3262e;
    --brand-red-deep: #9e1b22;
    --ink: #2a2a2a;
    --on-red: #ffffff;
  }
  html, body {
    margin: 0;
    width: 1200px;
    height: 818px;
    overflow: hidden;
    background: var(--page-bg);
  }
  .canvas {
    position: relative;
    width: 1200px;
    height: 818px;
  }
  .card {
    position: absolute;
    left: 120px;
    top: 135px;
    width: 960px;
    height: 548px;
    background: var(--card-white);
    box-shadow: 0 10px 30px rgba(0,0,0,0.18);
    overflow: hidden;
  }
  .card-shapes {
    position: absolute;
    inset: 0;
  }
  .brand {
    position: absolute;
    left: 30px;
    top: 160px;
    width: 380px;
    display: flex;
    flex-direction: column;
    align-items: center;
    gap: 26px;
  }
  .brand-mark {
    width: 110px;
    height: 110px;
    border-radius: 50%;
    border: 6px solid var(--brand-red);
    box-sizing: border-box;
  }
  .brand-name {
    margin: 0;
    font-family: "Cinzel", serif;
    font-weight: 500;
    font-size: 20px;
    line-height: 1.4;
    letter-spacing: 0.5px;
    color: var(--ink);
    text-align: center;
    white-space: nowrap;
  }
  .contact {
    position: absolute;
    left: 640px;
    top: 175px;
    width: 300px;
    color: var(--on-red);
    font-family: "Roboto", sans-serif;
  }
  .contact-name {
    margin: 0;
    font-family: "Great Vibes", cursive;
    font-weight: 400;
    font-size: 42px;
    line-height: 1.1;
    white-space: nowrap;
  }
  .contact-credentials {
    margin: 6px 0 2px 10px;
    font-size: 18px;
  }
  .contact-title {
    margin: 0 0 20px 10px;
    font-size: 18px;
  }
  .contact-line {
    display: flex;
    align-items: center;
    gap: 10px;
    margin: 0 0 8px 10px;
    font-size: 19px;
    white-space: nowrap;
  }
  .contact-icon {
    width: 20px;
    height: 20px;
    flex: none;
  }
</style>
</head>
<body>
<main class="canvas">
  <section class="card" aria-label="Business card">
    <svg class="card-shapes" viewBox="0 0 960 548" width="960" height="548" aria-hidden="true">
      <defs>
        <linearGradient id="redPanel" x1="0" y1="0" x2="1" y2="1">
          <stop offset="0" stop-color="#c3262e"/>
          <stop offset="1" stop-color="#9e1b22"/>
        </linearGradient>
      </defs>
      <path class="band-black" d="M380,0 H600 C620,200 560,420 440,548 H422 C520,400 520,180 380,0 Z" fill="var(--band-black)"/>
      <path class="panel-red" d="M612,0 H960 V548 H452 C572,420 632,200 612,0 Z" fill="url(#redPanel)" stroke="var(--card-white)" stroke-width="4"/>
    </svg>

    <div class="brand">
      <div class="brand-mark"></div>
      <h1 class="brand-name">Animal Care Oakmere Group<br>of Central PA</h1>
    </div>

    <div class="contact">
      <p class="contact-name">Tomás R. Quintaval</p>
      <p class="contact-credentials">DVM, MLAS, BS</p>
      <p class="contact-title">Managing Director</p>
      <p class="contact-line">
        <svg class="contact-icon" viewBox="0 0 24 24" aria-hidden="true">
          <rect x="1" y="1" width="22" height="22" rx="3" fill="var(--on-red)"/>
          <path d="M7 5 l3 0 l1 4 l-2 1.5 a9 9 0 0 0 4.5 4.5 l1.5 -2 l4 1 l0 3 a2 2 0 0 1 -2 2 a14 14 0 0 1 -12 -12 a2 2 0 0 1 2 -2 z" fill="var(--brand-red)"/>
        </svg>
        5552846017
      </p>
      <p class="contact-line">
        <svg class="contact-icon" viewBox="0 0 24 24" aria-hidden="true">
          <rect x="1" y="1" width="22" height="22" rx="3" fill="var(--on-red)"/>
          <rect x="5" y="7" width="14" height="10" fill="none" stroke="var(--brand-red)" stroke-width="1.8"/>
          <path d="M5 7 L12 13 L19 7" fill="none" stroke="var(--brand-red)" stroke-width="1.8"/>
        </svg>
        dvmtrq@mailbrook.net
      </p>
    </div>
  </section>
</main>
</body>
</html>
```